Infection control

to re-design website to include the benefits of powdered bleach packed in pre-measured sachets which when dissolved in water provides economy, efficacy and is safe to use with the use of costly packaging. We need new text outlining the benefits of the world's most commonly used disinfectant for major hospitals, institutions, pathology, military and disaster areas.

Translate design into coded website using CMS with the following features:
Mobile responsive using HTML 5/ CSS3 standards
Coded with SEO standards and with H1 tags for easy spidering and with Wordpress CMS with is page rank 9
Site migration
Email support
Updates

Target Market(s)

hospitals, institutions, pathology, military and disaster areas

Industry/Entity Type

Chemical Product

Number of Pages Required

4 page

Colors

Designer to choose colors to be used in the design.

Requirements
Must have
• factual information based on the efficiency of sodium hypochlorite (bleach) used for infection control. The many viruses, bacteria, pathogens etc which certain strengths of bleach eliminate upon contact.
• As tis is a redesign, existing pages including MSDS sheets to stay the same
Nice to have
• a new look and feel including current logos
Should not have
• incorrect info

```html
<!DOCTYPE html>
<html lang="en">
<head>
<meta charset="utf-8">
<title>Contact us – Chlorena</title>
<link rel="stylesheet" href="https://fonts.googleapis.com/css2?family=Kanit:wght@400;500&display=swap">
<style>
  :root{
    --green:#3fd21a;
    --green-soft:#9be36b;
    --green-btn-top:#b6ec7e;
    --green-btn-bottom:#7fcf3a;
    --ink:#111;
    --footer-bg:#222222;
    --white:#ffffff;
  }
  *{box-sizing:border-box;margin:0;padding:0}
  html,body{width:1200px;height:787px;overflow:hidden;background:var(--white)}
  body{font-family:"Kanit",sans-serif;color:var(--ink);position:relative}
  .page-title{position:absolute;left:513px;top:26px;width:174px;height:47px;display:flex;align-items:center;gap:12px;font-size:29px;font-weight:400;border-bottom:4px solid var(--green);padding-left:0;line-height:1}
  .page-title svg{width:22px;height:26px}
  .swoosh{position:absolute;left:0;top:0}
  .contact-panel{position:absolute;left:52px;top:157px;width:1098px;height:460px;border-radius:10px;overflow:hidden}
  .panel-photo{position:absolute;inset:0;background:
      linear-gradient(90deg,rgba(230,236,240,.9) 0%,rgba(214,226,232,.85) 35%,rgba(200,222,232,.8) 60%,rgba(120,180,215,.7) 75%,rgba(150,210,200,.8) 90%,rgba(160,220,140,.85) 100%),
      linear-gradient(180deg,#e9eef2 0%,#c9d8e2 60%,#b9ccd8 100%)}
  .panel-heading{position:absolute;left:0;width:100%;top:28px;text-align:center;font-size:22px;font-weight:500}
  .field-label{position:absolute;font-size:14px;font-weight:500}
  .field{position:absolute;border:2px solid var(--green-soft);border-radius:8px;background:rgba(255,255,255,.55)}
  .submit-btn{position:absolute;left:556px;top:406px;width:128px;height:35px;border-radius:7px;border:none;background:linear-gradient(var(--green-btn-top),var(--green-btn-bottom));box-shadow:0 2px 3px rgba(0,0,0,.35);font-family:"Kanit",sans-serif;font-size:19px;font-weight:500;color:#2c3a1e;letter-spacing:.5px}
  .site-footer{position:absolute;left:0;top:697px;width:1200px;height:90px;background:var(--footer-bg);color:var(--white)}
  .supplier-badge{position:absolute;left:46px;top:8px;width:90px;height:72px}
  .copyright{position:absolute;left:0;width:1200px;top:63px;text-align:center;font-size:14px}
  .footer-contact{position:absolute;left:970px;top:9px;font-size:14px;line-height:15.5px}
  .footer-contact h2{color:var(--green);font-size:21px;font-weight:500;line-height:24px;display:flex;align-items:center;gap:7px}
</style>
</head>
<body>
  <h1 class="page-title">
    <svg viewBox="0 0 22 26" aria-hidden="true"><circle cx="11" cy="8" r="6" fill="#111"/><path d="M1 26 C1 18 5 15 11 15 C17 15 21 18 21 26Z" fill="#111"/></svg>
    Contact us
  </h1>

  <svg class="swoosh" width="1200" height="787" aria-hidden="true">
    <path d="M52,153 C52,134 66,123 92,123 L900,150 L52,153Z" fill="var(--green)"/>
    <path d="M340,623 L1150,623 C1150,640 1132,649 1100,649Z" fill="var(--green)"/>
  </svg>

  <section class="contact-panel">
    <div class="panel-photo" role="img" aria-label="Blurred photo of a bright hospital corridor with staff in blue scrubs"></div>
    <p class="panel-heading">Please send us your Feedback and we will respond your enquiry as soon as possible.</p>
    <span class="field-label" style="left:106px;top:103px">First Name :</span>
    <div class="field" style="left:250px;top:92px;width:259px;height:39px"></div>
    <span class="field-label" style="left:586px;top:103px">Last Name :</span>
    <div class="field" style="left:730px;top:92px;width:259px;height:39px"></div>
    <span class="field-label" style="left:106px;top:163px">E-Mail :</span>
    <div class="field" style="left:250px;top:152px;width:739px;height:39px"></div>
    <span class="field-label" style="left:106px;top:213px">Message :</span>
    <div class="field" style="left:250px;top:216px;width:739px;height:166px"></div>
    <button class="submit-btn">SUBMIT</button>
  </section>

  <footer class="site-footer">
    <svg class="supplier-badge" viewBox="0 0 90 72" aria-hidden="true"><circle cx="45" cy="36" r="33" fill="none" stroke="var(--green)" stroke-width="3"/></svg>
    <p class="copyright">Copyright 2018 @ Chlorena ®</p>
    <div class="footer-contact">
      <h2>CONTACT US
        <svg width="18" height="18" viewBox="0 0 18 18" aria-hidden="true"><circle cx="9" cy="9" r="8" fill="none" stroke="var(--green)" stroke-width="1.6"/><path d="M5.5 12.5 L12.5 5.5" stroke="var(--green)" stroke-width="2" stroke-linecap="round"/></svg>
      </h2>
      <p>Phone : 1300 555 014</p>
      <p>Fax : 1300 555 018</p>
      <p>info@chlorenagroup.com</p>
    </div>
  </footer>
</body>
</html>
```